Satchel & Sundial needs new business card design

I need a new business card design. I'm looking for out-of-the-box design which represents the freedom of being a location independent entrepreneur.
I offer coaching, retreats and trips.
I would like to see designs with and without the photo.
Colors I use are black (#000000), green (#25A796) and brown (#D7C38C)
Website satchelandsundial.example

Target Market(s)

location independent entrepreneurs, digital nomads, people looking to swap the 9 to 5 for a lifestyle business

Industry/Entity Type

Business

Contact Information for Business Card

Dorota Falkner
Your Lifestyle Business Coach, Retreat & Trip Leader
http://satchelandsundial.example
hello@satchelandsundial.example
Live a life you don't need a holiday from

Font styles to use
Serif
Sans Serif

Requirements
Must have
• One side should contain only the logo. I would also consider having the "Live a life you don't need a holiday from" on that side too (depending on how it looks)
• Please show both sides on the designs.

```html
<!DOCTYPE html>
<html lang="en">
<head>
<meta charset="utf-8">
<title>Satchel &amp; Sundial business card</title>
<link rel="stylesheet" href="https://fonts.googleapis.com/css2?family=Raleway:wght@400;600;700&family=Lora:ital,wght@0,400;0,600;1,400&display=swap">
<style>
  :root {
    --backdrop: #5fcfbe;
    --charcoal: #2a292b;
    --charcoal-deep: #1f1e20;
    --paper: #f1f0ee;
    --teal: #25a796;
    --teal-soft: #8fe0d2;
    --white: #ffffff;
  }
  html, body {
    margin: 0;
    padding: 0;
    width: 1200px;
    height: 986px;
    overflow: hidden;
    background: var(--backdrop);
  }
  .canvas {
    width: 1200px;
    height: 986px;
    display: flex;
    flex-direction: column;
    align-items: center;
    justify-content: center;
    gap: 60px;
  }
  .card {
    width: 620px;
    height: 354px;
    position: relative;
    overflow: hidden;
    box-shadow: 0 18px 40px rgba(0, 60, 50, 0.28);
  }
  .card svg { position: absolute; inset: 0; }

  /* Front side */
  .card-front { background: linear-gradient(160deg, var(--charcoal) 0%, var(--charcoal-deep) 100%); }
  .front-wordmark {
    position: absolute;
    left: 0;
    top: 160px;
    width: 620px;
    text-align: center;
    transform: rotate(-5deg);
    font-family: "Raleway", sans-serif;
    font-weight: 700;
    font-size: 46px;
    letter-spacing: 2px;
    text-transform: uppercase;
    color: var(--charcoal);
  }

  /* Back side */
  .card-back { background: linear-gradient(160deg, var(--charcoal) 0%, var(--charcoal-deep) 100%); }
  .back-name {
    position: absolute;
    right: 30px;
    top: 24px;
    height: 50px;
    line-height: 50px;
    font-family: "Raleway", sans-serif;
    font-weight: 400;
    font-size: 28px;
    color: var(--white);
  }
  .back-brand {
    position: absolute;
    left: 26px;
    top: 120px;
    width: 230px;
  }
  .back-wordmark {
    font-family: "Raleway", sans-serif;
    font-weight: 700;
    font-size: 25px;
    line-height: 1.15;
    text-transform: uppercase;
    color: var(--charcoal);
    margin: 0 0 46px;
  }
  .back-role {
    font-family: "Lora", serif;
    font-size: 15px;
    line-height: 1.35;
    color: var(--teal);
    margin: 0;
  }
  .contact-list {
    position: absolute;
    left: 316px;
    top: 118px;
    margin: 0;
    padding: 0;
    list-style: none;
    font-family: "Lora", serif;
    font-size: 14px;
    color: var(--teal-soft);
  }
  .contact-list li { height: 44px; line-height: 44px; }
  .back-motto {
    position: absolute;
    right: 22px;
    bottom: 20px;
    font-family: "Lora", serif;
    font-weight: 600;
    font-size: 14px;
    color: var(--white);
    margin: 0;
  }
</style>
</head>
<body>
<main class="canvas">

  <section class="card card-front" aria-label="Card front">
    <svg width="620" height="354" viewBox="0 0 620 354" aria-hidden="true">
      <polygon class="front-band" points="0,150 620,96 620,236 0,290" fill="#f1f0ee"/>
      <line x1="380" y1="74" x2="620" y2="53" stroke="#25a796" stroke-width="4"/>
      <line x1="420" y1="84" x2="620" y2="66" stroke="#25a796" stroke-width="4"/>
      <line x1="0" y1="312" x2="230" y2="292" stroke="#25a796" stroke-width="4"/>
      <line x1="0" y1="325" x2="190" y2="308" stroke="#25a796" stroke-width="4"/>
    </svg>
    <div class="front-wordmark">Satchel &amp; Sundial</div>
  </section>

  <section class="card card-back" aria-label="Card back">
    <svg width="620" height="354" viewBox="0 0 620 354" aria-hidden="true">
      <rect class="name-band" x="0" y="24" width="620" height="50" fill="#25a796"/>
      <rect class="brand-panel" x="0" y="74" width="280" height="280" fill="#f1f0ee"/>
      <!-- envelope icon -->
      <circle cx="280" cy="140" r="15" fill="#f1f0ee" stroke="#25a796" stroke-width="2"/>
      <rect x="271" y="134" width="18" height="12" fill="none" stroke="#2a292b" stroke-width="1.6"/>
      <polyline points="271,134 280,141 289,134" fill="none" stroke="#2a292b" stroke-width="1.6"/>
      <!-- globe icon -->
      <circle cx="280" cy="184" r="15" fill="#f1f0ee" stroke="#25a796" stroke-width="2"/>
      <circle cx="280" cy="184" r="8" fill="none" stroke="#2a292b" stroke-width="1.6"/>
      <line x1="272" y1="184" x2="288" y2="184" stroke="#2a292b" stroke-width="1.3"/>
      <ellipse cx="280" cy="184" rx="3.5" ry="8" fill="none" stroke="#2a292b" stroke-width="1.3"/>
    </svg>
    <div class="back-name">Dorota Falkner</div>
    <div class="back-brand">
      <p class="back-wordmark">Satchel &amp; Sundial</p>
      <p class="back-role">Your Lifestyle Business Coach,<br>Retreat &amp; Trip Leader</p>
    </div>
    <ul class="contact-list">
      <li>hello@satchelandsundial.example</li>
      <li>www.satchelandsundial.example</li>
    </ul>
    <p class="back-motto">Live a life you don’t need a holiday from</p>
  </section>

</main>
</body>
</html>
```